Logo and Card design for KRV Home Solutions LLC

I need an edgier logo and business card designs. Current logo attached. I like the colors below. I would like the logo to incorporate a home in the design.
Title = Principal-Acquisitions
Email:KRVHOMESOLUTIONS@fernmail.example
555-214-0937
facebook
IG
2 sided business card with the front being contact info a slogan about selling a home fast. The back incorporating What we do. Buy houses, land, or commercial property as is. We find solutions to make the process of selling simple and fair.

Target Market(s)

Motivated house sellers.

Industry/Entity Type

Business

Contact Information for Business Card

Who we are: We are a Faith based Real Estate Investment Company. We pay cash for homes in any condition and can close quick. Whatever the reason you need to sell fast, we can help. We believe in creating win-win solutions to help you in your time of need. We care! We can help!

Logo Text

KRV Home Solutions LLC

Font styles to use
Sans Serif

Colors
33a6d7
0355a3
85abd2
cee9f5
9d9d9d
b2b2b2
ffffff

Requirements
Must have
• Old logo attached. I want something edgier.
• Company name, phone number, description on the back of what we can do. Pay all cash. Buy in as is condition. No fees,Commisions or closing costs.Close quick. No hassles with solutions to meet your unique situation.
• Call today for an offer within 24 hours.

```html
<!DOCTYPE html>
<html lang="en">
<head>
<meta charset="utf-8">
<title>KRV Home Solutions – Business Card</title>
<link rel="stylesheet" href="https://fonts.googleapis.com/css2?family=Work+Sans:wght@400;500;600&family=Oswald:wght@500&display=swap">
<style>
  :root {
    --stage: #2b2b2b;
    --navy: #203a82;
    --navy-text: #1e3577;
    --white: #ffffff;
    --ink: #555555;
    --rule: #8796b8;
  }
  * { margin: 0; padding: 0; box-sizing: border-box; }
  html, body { width: 1200px; height: 900px; overflow: hidden; }
  body {
    background: var(--stage);
    font-family: "Work Sans", sans-serif;
    display: flex;
    flex-direction: column;
    align-items: center;
    justify-content: center;
    gap: 36px;
  }
  .card {
    width: 700px;
    height: 400px;
    position: relative;
    overflow: hidden;
    box-shadow: 0 10px 30px rgba(0,0,0,.45);
  }

  /* Back of card */
  .card--back {
    background: var(--navy);
    color: var(--white);
    display: flex;
    flex-direction: column;
    align-items: center;
    justify-content: center;
    text-align: center;
  }
  .brand {
    display: flex;
    align-items: center;
    gap: 14px;
    margin-bottom: 44px;
  }
  .brand__mark {
    width: 22px;
    height: 22px;
    background: var(--white);
  }
  .brand__name {
    font-family: "Work Sans", sans-serif;
    font-weight: 600;
    font-size: 34px;
    letter-spacing: 2px;
    color: var(--white);
  }
  .pitch {
    font-size: 17px;
    line-height: 1.45;
    letter-spacing: .3px;
  }

  /* Front of card */
  .card--front {
    background: var(--white);
  }
  .identity {
    position: absolute;
    left: 50px;
    top: 142px;
    width: 260px;
  }
  .identity__name {
    font-family: "Oswald", sans-serif;
    font-weight: 500;
    font-size: 36px;
    line-height: 1;
    color: var(--navy-text);
    letter-spacing: -.5px;
    transform: scaleX(.82);
    transform-origin: left;
    white-space: nowrap;
  }
  .identity__title {
    font-size: 16px;
    color: var(--ink);
    margin-top: 4px;
    letter-spacing: .4px;
  }
  .divider {
    position: absolute;
    left: 325px;
    top: 112px;
    width: 1.5px;
    height: 108px;
    background: var(--rule);
  }
  .contacts {
    position: absolute;
    left: 345px;
    top: 110px;
    list-style: none;
  }
  .contacts li {
    display: flex;
    align-items: center;
    gap: 10px;
    font-size: 14px;
    color: var(--ink);
    height: 27px;
    letter-spacing: .2px;
    white-space: nowrap;
  }
  .contacts svg { width: 14px; height: 14px; flex: none; }
  .slogan {
    position: absolute;
    right: 150px;
    bottom: 70px;
    font-size: 16px;
    font-weight: 500;
    letter-spacing: 3.5px;
    color: #333333;
  }
</style>
</head>
<body>

  <section class="card card--back" aria-label="Card back">
    <div class="brand">
      <span class="brand__mark"></span>
      <span class="brand__name">KRV HOME SOLUTIONS</span>
    </div>
    <p class="pitch">
      Pay all cash. Buy in as is condition. No fees,Commisions<br>
      or closing costs.Close quick. No hassles with solutions<br>
      to meet your unique situation.<br>
      Call today for an offer within 24 hours.
    </p>
  </section>

  <section class="card card--front" aria-label="Card front">
    <div class="identity">
      <h1 class="identity__name">KRV HOME SOLUTIONS</h1>
      <p class="identity__title">Principal-Acquisitions</p>
    </div>
    <span class="divider"></span>
    <ul class="contacts">
      <li>
        <svg viewBox="0 0 14 14" aria-hidden="true"><circle cx="7" cy="7" r="7" fill="#1e3577"/><path d="M4.3 3.6l1.4-.3.7 1.8-.9.6a5 5 0 0 0 2.6 2.6l.6-.9 1.8.7-.3 1.4C7.3 9.6 4.4 6.7 4.3 3.6z" fill="#fff"/></svg>
        555-214-0937
      </li>
      <li>
        <svg viewBox="0 0 14 14" aria-hidden="true"><circle cx="7" cy="7" r="7" fill="#1e3577"/></svg>
        /krvhomesolutions
      </li>
      <li>
        <svg viewBox="0 0 14 14" aria-hidden="true"><circle cx="7" cy="7" r="7" fill="#1e3577"/></svg>
        @krvhomesolutions
      </li>
      <li>
        <svg viewBox="0 0 14 14" aria-hidden="true"><circle cx="7" cy="7" r="7" fill="#1e3577"/><rect x="3.5" y="4.5" width="7" height="5" fill="none" stroke="#fff" stroke-width="1"/><path d="M3.5 4.5L7 7.3l3.5-2.8" fill="none" stroke="#fff" stroke-width="1"/></svg>
        KRVHOMESOLUTIONS@fernmail.example
      </li>
    </ul>
    <p class="slogan">SELLING A HOME FAST</p>
  </section>

</body>
</html>
```